Accounting firm needing business card / letterhead designed
Marcus L. Trenholm, CPA
marcus@veltrowledger.com
www.veltrowledger.com
842 E Alder Ave Harlow Bend, WI 43827
419-562-0974

```html
<!DOCTYPE html>
<html lang="en">
<head>
<meta charset="utf-8">
<title>Veltro Ledger – Business Card</title>
<link rel="stylesheet" href="https://fonts.googleapis.com/css2?family=Roboto:wght@400;700&family=Roboto+Condensed:wght@500&display=swap">
<style>
  :root {
    --navy: #241f5e;
    --green: #7dc242;
    --paper: #f4f4f3;
    --ink-grey: #555a60;
    --white: #ffffff;
    --backdrop: #e6e3de;
    --pattern-a: #ebebee;
    --pattern-b: #e2e2e8;
  }
  * { box-sizing: border-box; margin: 0; padding: 0; }
  html, body { width: 1200px; height: 960px; overflow: hidden; }
  body {
    background: var(--backdrop);
    position: relative;
    font-family: "Roboto", Arial, sans-serif;
  }
  .card {
    position: absolute;
    width: 600px;
    height: 343px;
    background: var(--paper);
    box-shadow: 0 2px 4px rgba(0,0,0,.25);
    overflow: hidden;
  }
  .card--front { left: 314px; top: 113px; }
  .card--back  { left: 311px; top: 472px; }

  .contact-panel {
    position: absolute; left: 0; top: 0;
    width: 285px; height: 100%;
    background: var(--navy);
    color: var(--white);
    padding: 96px 0 0 42px;
  }
  .contact-name {
    font-family: "Roboto Condensed", "Arial Narrow", sans-serif;
    font-weight: 500;
    font-size: 21px;
    color: var(--green);
    line-height: 1;
    margin-bottom: 25px;
  }
  .contact-address { font-size: 14px; line-height: 19px; margin-bottom: 11px; }
  .contact-list { list-style: none; font-size: 14px; line-height: 19px; }
  .contact-list li { display: flex; align-items: center; gap: 9px; }
  .contact-list svg { width: 13px; height: 13px; fill: var(--green); flex: none; }

  .accent-stripe {
    position: absolute; right: 0; top: 0;
    width: 15px; height: 100%;
    background: var(--green);
  }
  .brand-name {
    position: absolute;
    font-family: "Roboto", Arial, sans-serif;
    font-weight: 700;
    color: var(--navy);
    letter-spacing: 2px;
    white-space: nowrap;
    text-align: center;
  }
  .card--front .brand-name { left: 285px; width: 300px; top: 160px; font-size: 30px; }

  .pattern-field {
    position: absolute; inset: 0;
    background: linear-gradient(135deg, var(--pattern-a), var(--pattern-b) 50%, var(--pattern-a));
  }
  .card--back .brand-name { left: 0; width: 100%; top: 118px; font-size: 50px; letter-spacing: 3px; }
  .back-website {
    position: absolute; left: 0; width: 100%; top: 283px;
    text-align: center;
    font-size: 14px;
    letter-spacing: 5px;
    color: var(--ink-grey);
  }
</style>
</head>
<body>
  <section class="card card--front">
    <div class="contact-panel">
      <h1 class="contact-name">Marcus L. Trenholm, CPA</h1>
      <p class="contact-address">842 E Alder Ave<br>Harlow Bend, WI 43827</p>
      <ul class="contact-list">
        <li><svg viewBox="0 0 16 16"><path d="M3.6 1.2l2.3 2.4c.4.4.4 1 0 1.4L4.8 6.2a9 9 0 0 0 5 5l1.2-1.1c.4-.4 1-.4 1.4 0l2.4 2.3c.4.4.4 1 0 1.4l-1.3 1.3C11 16.6 -.6 5 .9 3.6L2.2 2.2c.4-.4 1-.4 1.4-1z"/></svg>419-562-0974</li>
        <li><svg viewBox="0 0 16 16"><path d="M0 3h16v1.5L8 9 0 4.5z"/><path d="M0 6.2l8 4.5 8-4.5V13H0z"/></svg>marcus@veltrowledger.com</li>
        <li><svg viewBox="0 0 16 16"><circle cx="8" cy="8" r="7.5"/><path d="M4 5c1 0 2 1 2 2s-1 1-1 2 1 2 0 3M10 2c0 1 1 2 2 2s1 2 0 3 1 2 2 2" stroke="#241f5e" stroke-width="1.4" fill="none"/></svg>www.veltrowledger.com</li>
      </ul>
    </div>
    <p class="brand-name">VELTRO LEDGER</p>
    <div class="accent-stripe"></div>
  </section>

  <section class="card card--back">
    <div class="pattern-field" role="img" aria-label="Faint diagonal repeating brand-name pattern across the card"></div>
    <p class="brand-name">VELTRO LEDGER</p>
    <p class="back-website">www.veltrowledger.com</p>
  </section>
</body>
</html>
```